Insert card for anti-slip sticker

Product packaging should be inspired by the following
packaging and stand out at the same time: https://bxlo.example/7QwRtvk

The packaging is not packaging in the conventional sense, but rather a kind of insert card that can be opened.
This can also be found in the linked product.

On the front of the card: Product name (20 anti-slip strips), advantages of the product and a appealing picture with the product

Inside: Instructions for use and product tips

Back: Images with possible uses, company headquarters, email for contact purposes, note about positive evaluation on Veltora

```html
<!DOCTYPE html>
<html lang="en">
<head>
<meta charset="utf-8">
<title>Mira Vale – 20 Anti-Slip Strips Insert Card</title>
<link href="https://fonts.googleapis.com/css2?family=Montserrat:wght@400;500;600&display=swap" rel="stylesheet">
<style>
  :root{
    --page:#e9e7e4;
    --ink:#1b1b1c;
    --band:#232324;
    --gold:#d4ad4a;
    --gold-soft:#e6c772;
    --marble:#f3f2ef;
    --marble-vein:#dedcd8;
    --photo-dark:#2a2a2b;
    --photo-mid:#7d7b78;
    --photo-light:#c9c6c1;
    --skin:#c9a083;
  }
  *{box-sizing:border-box;margin:0;padding:0}
  html,body{width:1200px;height:971px;overflow:hidden;background:var(--page)}
  body{font-family:"Montserrat",Arial,sans-serif;position:relative}
  .insert-card{
    position:absolute;left:400px;top:35px;width:400px;height:900px;
    background:var(--marble);
    box-shadow:0 10px 30px rgba(0,0,0,.18);
    overflow:hidden;
  }
  .insert-card svg.card-art{position:absolute;inset:0;width:100%;height:100%}
  .benefit-list{position:absolute;left:28px;top:220px;list-style:none}
  .benefit{
    display:flex;flex-direction:column;align-items:center;
    width:84px;margin-bottom:14px;
  }
  .benefit-icon{
    width:62px;height:62px;border-radius:50%;
    background:var(--ink);border:2px solid var(--gold);
    display:flex;align-items:center;justify-content:center;
  }
  .benefit-label{
    margin-top:4px;font-size:10px;color:#f2f2f2;letter-spacing:.3px;
    text-shadow:0 1px 2px rgba(0,0,0,.6);white-space:nowrap;
  }
  .brand{
    position:absolute;left:0;right:0;top:618px;
    display:flex;flex-direction:column;align-items:center;
  }
  .brand-dot{width:32px;height:32px;border-radius:50%;background:var(--ink)}
  .brand-name{
    margin-top:6px;font-size:28px;font-weight:500;color:var(--gold);letter-spacing:1px;line-height:1.1;
  }
  .product-badge{
    position:absolute;left:50px;right:50px;top:790px;height:86px;
    border:1.5px solid var(--gold);border-radius:14px;
    display:flex;flex-direction:column;align-items:center;justify-content:center;
  }
  .product-title{display:flex;align-items:center;color:var(--gold-soft)}
  .product-count{font-size:36px;font-weight:400;line-height:1;padding-right:12px}
  .product-name{
    border-left:1.5px solid var(--gold);padding-left:12px;
    font-size:15px;font-weight:500;line-height:1.15;letter-spacing:1px;
  }
  .usage-pill{
    margin-top:8px;padding:3px 14px;border:1px solid var(--gold);border-radius:20px;
    font-size:9.5px;color:#f1f1f1;letter-spacing:.8px;white-space:nowrap;
  }
</style>
</head>
<body>
<main class="insert-card">
  <svg class="card-art" viewBox="0 0 400 900">
    <defs>
      <linearGradient id="photoTone" x1="0" y1="0" x2="1" y2="1">
        <stop offset="0" stop-color="var(--photo-light)"/>
        <stop offset=".45" stop-color="var(--photo-mid)"/>
        <stop offset="1" stop-color="var(--photo-dark)"/>
      </linearGradient>
      <linearGradient id="skinTone" x1="0" y1="0" x2="1" y2="1">
        <stop offset="0" stop-color="#b79a86"/>
        <stop offset="1" stop-color="#8d7a6c"/>
      </linearGradient>
      <linearGradient id="marbleTone" x1="0" y1="0" x2="1" y2="1">
        <stop offset="0" stop-color="#faf9f7"/>
        <stop offset="1" stop-color="var(--marble-vein)"/>
      </linearGradient>
    </defs>
    <rect class="marble-panel" width="400" height="900" fill="url(#marbleTone)"/>
    <g role="img" aria-label="Photo of bare feet standing on a shower floor fitted with anti-slip strips under running water">
      <path class="hero-photo" d="M0 0 H400 V540 Q220 570 0 640 Z" fill="url(#photoTone)"/>
      <path class="backdrop-photo" d="M40 0 Q190 230 400 300 V0 Z" fill="url(#skinTone)"/>
    </g>
    <path class="gold-arc" d="M40 0 Q190 230 400 300" fill="none" stroke="var(--gold)" stroke-width="3"/>
    <path class="base-band" d="M0 740 Q200 690 400 660 V900 H0 Z" fill="var(--band)"/>
  </svg>

  <ul class="benefit-list">
    <li class="benefit">
      <span class="benefit-icon">
        <svg width="30" height="30" viewBox="0 0 30 30"><path d="M6 16 l6 6 l12 -14" fill="none" stroke="#fff" stroke-width="2.5"/></svg>
      </span>
      <span class="benefit-label">Non Slip</span>
    </li>
    <li class="benefit">
      <span class="benefit-icon">
        <svg width="30" height="30" viewBox="0 0 30 30"><path d="M15 4 C10 12 8 15 8 19 a7 7 0 0 0 14 0 C22 15 20 12 15 4Z" fill="#fff"/></svg>
      </span>
      <span class="benefit-label">Waterproof</span>
    </li>
    <li class="benefit">
      <span class="benefit-icon">
        <svg width="30" height="30" viewBox="0 0 30 30"><path d="M5 24 H25 M9 24 V10 l6 -5 l6 5 V24" fill="none" stroke="#fff" stroke-width="2.2"/></svg>
      </span>
      <span class="benefit-label">Easy Assembly</span>
    </li>
  </ul>

  <div class="brand">
    <span class="brand-dot"></span>
    <span class="brand-name">Mira Vale</span>
  </div>

  <div class="product-badge">
    <div class="product-title">
      <span class="product-count">20</span>
      <span class="product-name">ANTI-SLIP<br>STRIPS</span>
    </div>
    <span class="usage-pill">BATH / SHOWER / TUB / WET AREA</span>
  </div>
</main>
</body>
</html>
```